Business Card Design for Occupational Medicine Start Up Company

We need to design a professional business card. We are a healthcare company providing occupational medicine services to blue collar industries. We are professional, efficient and high quality service providers.

Target Market(s)

Blue Collar Industry: Shipbuilding, Ports, Trucking Companies; The Executives and Safety Officers for these companies

Industry/Entity Type

Healthcare

Contact Information for Business Card

Logo, Name, Title, Email, Phone

Other font styles liked:
• Please match our Brand Guide

Requirements
Must have
• Our Company Colors and Logo

```html
<!DOCTYPE html>
<html lang="en">
<head>
<meta charset="utf-8">
<title>Crewline Health Business Card</title>
<link href="https://fonts.googleapis.com/css2?family=Montserrat:wght@600;700&family=Roboto:wght@400;700&display=swap" rel="stylesheet">
<style>
  :root {
    --navy: #28348f;
    --navy-deep: #1f2a7a;
    --orange: #e07a2c;
    --amber: #f0b143;
    --white: #ffffff;
    --ink: #1d1d2b;
    --backdrop: #e9e9ec;
  }
  * { margin: 0; padding: 0; box-sizing: border-box; }
  html, body { width: 1200px; height: 912px; overflow: hidden; background: var(--backdrop); }
  .canvas { position: relative; width: 1200px; height: 912px; }
  .card {
    position: absolute; left: 320px; width: 560px; height: 320px;
    overflow: hidden; box-shadow: 0 8px 24px rgba(0,0,0,.18);
  }
  .card--front { top: 96px; background: var(--navy); }
  .card--back { top: 496px; background: var(--white); }

  .front-pattern {
    position: absolute; inset: 0;
    background: radial-gradient(circle at 50% 50%, #3040a4 0%, var(--navy) 55%, var(--navy-deep) 100%);
  }
  .front-brand {
    position: absolute; left: 50%; top: 50%; transform: translate(-50%, -50%);
    display: flex; align-items: center; gap: 14px; white-space: nowrap;
  }
  .brand-dot { width: 36px; height: 36px; border-radius: 50%; background: var(--white); }
  .brand-name {
    font-family: "Montserrat", sans-serif; font-weight: 700;
    font-size: 30px; letter-spacing: 1px; color: var(--white);
  }

  .back-brand {
    position: absolute; left: 40px; top: 84px; width: 250px;
    display: flex; flex-direction: column; align-items: center; gap: 12px;
  }
  .back-brand .brand-dot { width: 56px; height: 56px; background: var(--navy); }
  .back-brand .brand-name { color: var(--navy); font-size: 23px; letter-spacing: .5px; }

  .divider { position: absolute; left: 302px; top: 42px; width: 2px; height: 108px; background: var(--amber); }
  .contact { position: absolute; left: 320px; top: 38px; font-family: "Roboto", sans-serif; color: var(--ink); white-space: nowrap; }
  .contact-name { font-weight: 700; font-size: 21px; color: var(--navy); letter-spacing: .3px; }
  .contact-title { font-size: 12px; margin-top: 2px; margin-bottom: 10px; }
  .contact-line { display: flex; align-items: center; gap: 6px; font-size: 13px; line-height: 19px; }
  .contact-line svg { width: 11px; height: 11px; flex: none; }

  .wave { position: absolute; left: 0; bottom: 0; width: 560px; height: 166px; }
</style>
</head>
<body>
<main class="canvas">
  <section class="card card--front">
    <div class="front-pattern" role="img" aria-label="Repeating embossed brand pattern on navy"></div>
    <div class="front-brand">
      <span class="brand-dot"></span>
      <span class="brand-name">CREWLINEHEALTH</span>
    </div>
  </section>

  <section class="card card--back">
    <div class="back-brand">
      <span class="brand-dot"></span>
      <span class="brand-name">CREWLINEHEALTH</span>
    </div>
    <div class="divider"></div>
    <div class="contact">
      <div class="contact-name">MARCUS DELANEY</div>
      <div class="contact-title">Director</div>
      <div class="contact-line">
        <svg viewBox="0 0 12 12"><path d="M3 1l2 2.5-1 1.2a7 7 0 003.3 3.3l1.2-1L11 9l-1 2C5 11 1 7 1 2z" fill="var(--navy)"/></svg>
        (555)014 2290
      </div>
      <div class="contact-line">
        <svg viewBox="0 0 12 12"><rect x="1" y="2.5" width="10" height="7" fill="var(--navy)"/><path d="M1 2.5l5 4 5-4" stroke="#fff" stroke-width="1" fill="none"/></svg>
        info@crewlinehealth.com
      </div>
      <div class="contact-line">
        <svg viewBox="0 0 12 12"><circle cx="6" cy="6" r="5" fill="none" stroke="var(--navy)" stroke-width="1.2"/><path d="M1 6h10M6 1c-2 3-2 7 0 10M6 1c2 3 2 7 0 10" stroke="var(--navy)" stroke-width=".9" fill="none"/></svg>
        www.crewlinehealth.com
      </div>
    </div>
    <svg class="wave" viewBox="0 0 560 166" preserveAspectRatio="none">
      <path d="M0 166 L0 154 C160 146 250 124 340 64 C420 18 490 6 560 4 L560 166 Z" fill="var(--orange)"/>
      <path d="M0 166 L0 158 C160 150 252 130 342 72 C422 26 490 14 560 12 L560 166 Z" fill="var(--white)"/>
      <path d="M0 166 L0 161 C160 155 256 136 346 80 C424 34 492 22 560 20 L560 166 Z" fill="var(--navy)"/>
    </svg>
  </section>
</main>
</body>
</html>
```